Fun, Clean Business Card For Family Focused Travel Agency

I need a business card using specific colors and fonts as in the uploaded files. Ideally, I would like a large image of the logo on the back and all the contact info on the front. Maybe the stars/dots somewhere in a flowy form.

I do want it the contact information to be clear and easy to read. I don't want it to look too busy. Maybe even a bit minimalist.

I plan or ordering the ROUNDED CORNER business cards from Cardwell Press, so please consider that in your design.

Target Market(s)

Families with children, couples, groups of friends

Contact Information for Business Card

Marla Quint, Owner
Marla@TumbleTrips.example
Cell Phone Number 555-218-4603
Office Phone Number 555-647-1925
Specializing in Glimmerland destinations, Pelican Bay Fun Park, Cruises and All-Inclusive Vacations.

Nice but not required:
www.TumbleTrips.example
Facebook, Instagram, Twitter icons with username: TumbleTrips

Font styles to use
Sans Serif

Requirements
Must have
• Please try to use the colors from the logo as much as possible. I understand lighter shades/colors may be needed for some things.
Should not have
• NO SERIF FONTS. That is really the only thing I do not want at all

```html
<!DOCTYPE html>
<html lang="en">
<head>
<meta charset="utf-8">
<title>Tumble Trips – Business Card</title>
<link rel="stylesheet" href="https://fonts.googleapis.com/css2?family=Ubuntu:wght@400;500&family=Pacifico&display=swap">
<style>
  :root {
    --navy: #2b2f57;
    --navy-deep: #23274a;
    --ink: #2f3252;
    --teal: #2fb79a;
    --paper: #ffffff;
    --stage: #eeeef1;
    --mist-grey: #d9dadd;
    --mist-mint: #dcefe9;
    --mist-peach: #f6e6dc;
  }
  * { box-sizing: border-box; margin: 0; padding: 0; }
  html, body {
    width: 1200px; height: 1087px; overflow: hidden;
    background: var(--stage);
    font-family: "Ubuntu", sans-serif;
  }
  .sheet {
    width: 1200px; height: 1087px;
    display: flex; flex-direction: column; align-items: center; justify-content: center;
    gap: 44px;
  }
  .card {
    position: relative;
    width: 840px; height: 480px;
    border-radius: 34px;
    overflow: hidden;
    box-shadow: 0 10px 30px rgba(40, 44, 80, 0.12);
  }

  /* Front */
  .card--front { background: var(--paper); }
  .holder { position: absolute; left: 64px; top: 58px; }
  .holder__name {
    font-family: "Pacifico", cursive;
    font-size: 64px; line-height: 1.1;
    color: var(--ink);
  }
  .holder__role {
    margin-top: 2px; margin-left: 10px;
    font-size: 30px; color: var(--teal);
  }
  .contacts {
    position: absolute; left: 64px; top: 246px;
    list-style: none;
  }
  .contacts__item {
    display: flex; align-items: center; gap: 16px;
    font-size: 26px; line-height: 46px; color: var(--ink);
  }
  .contacts__icon { width: 22px; height: 22px; flex: none; }
  .contacts__icon * { stroke: var(--teal); fill: none; stroke-width: 1.8; stroke-linecap: round; stroke-linejoin: round; }
  .front-art {
    position: absolute; right: 30px; top: 150px;
    width: 360px; height: 330px;
    border-radius: 50% 50% 0 0;
    background: radial-gradient(ellipse at 55% 55%, var(--mist-grey) 0%, var(--mist-mint) 40%, var(--mist-peach) 62%, rgba(255,255,255,0) 78%);
    opacity: 0.7;
  }

  /* Back */
  .card--back {
    background: linear-gradient(180deg, #3a3e66 0%, var(--navy) 45%, var(--navy-deep) 100%);
    display: flex; align-items: center; justify-content: center;
  }
  .brand { display: flex; align-items: center; gap: 22px; }
  .brand__dot { width: 54px; height: 54px; border-radius: 50%; background: var(--paper); }
  .brand__name {
    font-size: 76px; font-weight: 500; color: var(--paper);
    letter-spacing: 1px;
  }
</style>
</head>
<body>
<main class="sheet">

  <section class="card card--front" aria-label="Business card front">
    <div class="holder">
      <h1 class="holder__name">Marla Quint</h1>
      <p class="holder__role">Owner</p>
    </div>
    <ul class="contacts">
      <li class="contacts__item">
        <svg class="contacts__icon" viewBox="0 0 24 24" aria-hidden="true"><rect x="7" y="2" width="10" height="20" rx="2"/><line x1="11" y1="18.5" x2="13" y2="18.5"/></svg>
        555-218-4603
      </li>
      <li class="contacts__item">
        <svg class="contacts__icon" viewBox="0 0 24 24" aria-hidden="true"><path d="M7 3 L10 7 L8 9.5 C9.5 12.5 11.5 14.5 14.5 16 L17 14 L21 17 L19 20.5 C11 20 4 13 3.5 5 Z"/></svg>
        555-647-1925
      </li>
      <li class="contacts__item">
        <svg class="contacts__icon" viewBox="0 0 24 24" aria-hidden="true"><rect x="2.5" y="5" width="19" height="14" rx="1"/><path d="M2.5 5.5 L12 13 L21.5 5.5"/></svg>
        Marla@TumbleTrips.example
      </li>
      <li class="contacts__item">
        <svg class="contacts__icon" viewBox="0 0 24 24" aria-hidden="true"><circle cx="12" cy="12" r="9.5"/><ellipse cx="12" cy="12" rx="4.5" ry="9.5"/><line x1="2.5" y1="12" x2="21.5" y2="12"/><path d="M4 7 H20 M4 17 H20"/></svg>
        www.TumbleTrips.example
      </li>
    </ul>
    <div class="front-art" role="img" aria-label="Faint pastel sailing ship emblem with scattered stars and dots"></div>
  </section>

  <section class="card card--back" aria-label="Business card back">
    <div class="brand">
      <span class="brand__dot" aria-hidden="true"></span>
      <span class="brand__name">Tumble Trips</span>
    </div>
  </section>

</main>
</body>
</html>
```